HearthMile business card and stationary design

We are looking for a simple yet elegant design for our mortgage company business card and stationary.

The card should include:
Name (Marcus Pell)
Title (CEO)
Phone Number (732-555-0182)
Address (48 Birchwell Court, Suite 314, Hazlet, NJ 07730)
Email (email@hearthmile.example)
"NMLS" i.e. (NMLS 61947)
"Company NMLS" (Company NMLS 274615)

Contact Information for Business Card

See above

```html
<!DOCTYPE html>
<html lang="en">
<head>
<meta charset="utf-8">
<title>HearthMile Business Card</title>
<link rel="stylesheet" href="https://fonts.googleapis.com/css2?family=Figtree:wght@400;500;700;800&display=swap">
<style>
  :root {
    --sky: #25aee4;
    --navy: #1a2633;
    --paper: #ffffff;
    --backdrop: #e9eaec;
  }
  * { margin: 0; padding: 0; box-sizing: border-box; }
  html, body {
    width: 1200px; height: 1200px; overflow: hidden;
    background: var(--backdrop);
    font-family: "Figtree", Arial, sans-serif;
  }
  .card {
    position: absolute;
    left: 228px;
    width: 745px; height: 427px;
    background: var(--paper);
    overflow: hidden;
  }
  .card--front { top: 114px; }
  .card--back { top: 583px; }

  .front-shape { position: absolute; inset: 0; }

  .contact {
    position: absolute; left: 42px; top: 82px;
    color: var(--paper);
  }
  .contact__name {
    font-weight: 800; font-size: 25px; letter-spacing: 0.3px; line-height: 1;
  }
  .contact__title {
    font-weight: 700; font-size: 19px; margin-top: 9px; line-height: 1;
  }
  .contact__address {
    font-size: 19px; line-height: 27px; margin-top: 20px; font-weight: 500;
  }
  .contact__list { list-style: none; margin-top: 16px; }
  .contact__item {
    display: flex; align-items: center; gap: 14px;
    font-size: 19px; line-height: 30px; font-weight: 500;
  }
  .contact__item svg { width: 19px; height: 19px; flex: none; }
  .contact__licence {
    font-size: 19px; line-height: 30px; margin-top: 12px; font-weight: 500;
  }

  .wordmark {
    position: absolute;
    color: var(--navy);
    font-weight: 700;
    line-height: 1;
    white-space: nowrap;
    letter-spacing: -0.5px;
    transform: translate(-50%, -50%);
  }
  .card--front .wordmark { left: 566px; top: 222px; font-size: 60px; }
  .card--back .wordmark { left: 50%; top: 228px; font-size: 94px; }
</style>
</head>
<body>

<section class="card card--front">
  <svg class="front-shape" viewBox="0 0 745 427" aria-hidden="true">
    <rect width="745" height="427" fill="var(--sky)"/>
    <circle cx="673" cy="221" r="336" fill="var(--navy)"/>
    <circle cx="755" cy="215" r="398" fill="var(--paper)"/>
  </svg>

  <div class="contact">
    <h1 class="contact__name">MARCUS PELL</h1>
    <p class="contact__title">CEO</p>
    <p class="contact__address">48 Birchwell Court, Suite 314,<br>Ferncastle, NJ 08999</p>
    <ul class="contact__list">
      <li class="contact__item">
        <svg viewBox="0 0 24 24" fill="none" stroke="currentColor" stroke-width="2.2" stroke-linecap="round" stroke-linejoin="round"><path d="M5 3h4l2 5-3 2a11 11 0 0 0 6 6l2-3 5 2v4a2 2 0 0 1-2 2A17 17 0 0 1 3 5a2 2 0 0 1 2-2z"/></svg>
        <span>732-555-0182</span>
      </li>
      <li class="contact__item">
        <svg viewBox="0 0 24 24" fill="currentColor"><path d="M2 5h20v14H2z"/><path d="M2 5l10 8 10-8" fill="none" stroke="var(--sky)" stroke-width="1.8"/></svg>
        <span>email@hearthmile.example</span>
      </li>
      <li class="contact__item">
        <svg viewBox="0 0 24 24" fill="none" stroke="currentColor" stroke-width="2"><circle cx="12" cy="12" r="10" fill="currentColor"/><path d="M2 12h20M12 2c3 3 3 17 0 20M12 2c-3 3-3 17 0 20" stroke="var(--sky)" stroke-width="1.4"/></svg>
        <span>www.hearthmile.example</span>
      </li>
    </ul>
    <p class="contact__licence">Company NMLS 274615<br>"NMLS" i.e. (NMLS 61947)</p>
  </div>

  <p class="wordmark">HearthMile</p>
</section>

<section class="card card--back">
  <p class="wordmark">HearthMile</p>
</section>

</body>
</html>
```